New Business Card Design Project

We require a business card design for Vexalund, a newly established Indian company.
Our focus is on the development, manufacturing, and export of a diverse array of pharmaceutical products on a global scale. The card should convey a professional appearance, as our primary markets are in Africa, China, and Southeast Asian nations.
We envision a two-sided business card, with the reverse side dedicated to a logo set against a solid color or an elegantly designed pattern. The corners should be rounded. We would appreciate seeing both horizontal and vertical design options. We trust the designer to utilize their expertise in creating this design.

The content for the business card is included in the attached Word file.

Target Market(s)

Our primary markets are in Africa, China, and Southeast Asian, Latin America, Maldives, Sri Lanka

Industry/Entity Type

Pharmaceutical Manufacturing and Export

Contact Information for Business Card

Colors

Designer to choose colors to be used in the design.

Requirements
Must have
• The reverse side of the business card features solely the logo along with the tagline, "Care in Every Dose."
Should not have
• The logo should not exceed two instances, encompassing both the front and back sides of the card.

```html
<!DOCTYPE html>
<html lang="en">
<head>
<meta charset="utf-8">
<title>Vexalund Business Card</title>
<link href="https://fonts.googleapis.com/css2?family=Montserrat:ital,wght@0,400;0,600;0,700;1,800&display=swap" rel="stylesheet">
<style>
  :root {
    --backdrop: #3a3a3a;
    --card-white: #ffffff;
    --brand-blue: #27a9e1;
    --brand-coral: #f06351;
    --ink: #3b3b3b;
  }
  * { margin: 0; padding: 0; box-sizing: border-box; }
  html, body {
    width: 1200px; height: 1111px; overflow: hidden;
    background: var(--backdrop);
    font-family: "Montserrat", sans-serif;
  }
  .card {
    position: absolute; left: 304px; width: 584px; height: 334px;
  }
  .card-front { top: 180px; background: var(--card-white); }
  .card-back { top: 598px; background: var(--brand-blue); }

  .front-brand {
    position: absolute; left: 36px; top: 28px;
    font-size: 56px; font-weight: 600; color: var(--brand-blue);
    letter-spacing: -0.5px; line-height: 1;
  }
  .holder-name {
    position: absolute; left: 39px; top: 116px;
    font-size: 22px; font-weight: 700; line-height: 1;
  }
  .holder-name .first { color: var(--brand-blue); }
  .holder-name .rest { color: var(--brand-coral); }
  .holder-role {
    position: absolute; left: 40px; top: 147px;
    font-size: 15px; color: var(--ink); letter-spacing: 1px;
  }
  .address {
    position: absolute; left: 41px; top: 186px;
    font-size: 15px; line-height: 20px; color: var(--ink); letter-spacing: 1.2px;
    font-style: normal;
  }
  .contacts { position: absolute; left: 39px; top: 238px; list-style: none; }
  .contacts li {
    display: flex; align-items: center; height: 21px;
    font-size: 15px; color: var(--ink); letter-spacing: 1px;
  }
  .contacts svg { width: 15px; height: 15px; margin-right: 8px; flex: none; }
  .front-mark { position: absolute; left: 347px; top: 115px; }

  .back-mark { position: absolute; left: 252px; top: 98px; }
  .back-brand {
    position: absolute; left: 0; right: 0; top: 205px;
    text-align: center; font-size: 52px; font-weight: 600;
    color: var(--card-white); letter-spacing: -0.5px; line-height: 1;
  }
  .tagline {
    position: absolute; left: 0; right: 0; top: 294px;
    text-align: center; font-size: 15px; font-weight: 800; font-style: italic;
    color: var(--card-white); letter-spacing: 1.5px;
  }
</style>
</head>
<body>
  <section class="card card-front">
    <div class="front-brand">Vexalund</div>
    <div class="holder-name"><span class="first">Ravin</span> <span class="rest">K. Tholane</span></div>
    <div class="holder-role">CEO</div>
    <address class="address">12, Sarovar Colony<br>Nashik, 422001, India</address>
    <ul class="contacts">
      <li>
        <svg viewBox="0 0 16 16" aria-hidden="true"><circle cx="8" cy="8" r="8" fill="var(--brand-blue)"/><path d="M5 4.2l1.4-.4 1 2-.9.8c.4 1 1.2 1.8 2.2 2.2l.8-.9 2 1-.4 1.4c-3.3.2-6.3-2.8-6.1-6.1z" fill="#fff"/></svg>
        +919800412735
      </li>
      <li>
        <svg viewBox="0 0 16 16" aria-hidden="true"><circle cx="8" cy="8" r="8" fill="var(--brand-coral)"/><rect x="4" y="5.2" width="8" height="5.6" rx="1" fill="#fff"/><path d="M4.3 5.6L8 8.3l3.7-2.7" stroke="var(--brand-coral)" stroke-width="1" fill="none"/></svg>
        rtholane@vexalund.com
      </li>
      <li>
        <svg viewBox="0 0 16 16" aria-hidden="true"><circle cx="8" cy="8" r="8" fill="var(--brand-blue)"/><circle cx="8" cy="8" r="4.2" stroke="#fff" stroke-width="1" fill="none"/><path d="M3.8 8h8.4M8 3.8c-2 2.4-2 6 0 8.4M8 3.8c2 2.4 2 6 0 8.4" stroke="#fff" stroke-width="0.9" fill="none"/></svg>
        vexalund.com
      </li>
    </ul>
    <svg class="front-mark" width="170" height="170" viewBox="0 0 170 170" aria-hidden="true">
      <circle cx="85" cy="85" r="85" fill="var(--brand-blue)"/>
    </svg>
  </section>

  <section class="card card-back">
    <svg class="back-mark" width="80" height="80" viewBox="0 0 80 80" aria-hidden="true">
      <circle cx="40" cy="40" r="40" fill="var(--card-white)"/>
    </svg>
    <div class="back-brand">Vexalund</div>
    <div class="tagline">Care in Every Dose.</div>
  </section>
</body>
</html>
```